An e-flyer for an exotic car and fine wine club.

This is the first meeting of Birchwell Motor Society and includes several businesses. Their logos should be featured at the bottom. It should be sleek, elegant and simple featuring a photo of an Varenne Coupe R7 as well as my logo (I will provide photos). The flyer needs to look professional and appeal to billionaires.
The text should read:
Birchwell Motor society presents
Quick Wheels and Rare Vintages (but not while driving)
Hosted by Halvorn Keep Vault
Bring your best car(s) and join us to enjoy the party with sommelier selected wines, the best classic and modern cars and hors d'oeuvre catered by Pembry's Shellfish Bar. Live DJ.
August 26th 3-6 p.m.
This event is gratis.
RSVP to nora@birchwellmotors.example for address and details

Target Market(s)
Very wealthy exotic car owners
Industry/Entity Type
Car Club, Fine Wines.
Requirements
Must have
- Style, panache, elegance, sleekness, simplicity. I like the idea of a black or dark flyer with a consistent color scheme.
Nice to have
- I want the flyer to be simple and sleek, feature an Varenne Coupe R7 as the eye catcher, Birchwell Motor Society logo featured prominently on the top, and the other business logos on the bottom.
Should not have
- It must not be too noisy or busy.

```html
<!DOCTYPE html>
<html lang="en">
<head>
<meta charset="utf-8">
<title>Quick Wheels and Rare Vintages — Birchwell Motor Society</title>
<link rel="stylesheet" href="https://fonts.googleapis.com/css2?family=Montserrat:wght@400;500;600;700&family=Open+Sans:wght@400;600&display=swap">
<style>
  :root {
    --paper: #ffffff;
    --ink: #1a1a1a;
    --accent: #e0282b;
    --brand: #2a2a2e;
    --track: #9c9a98;
    --car: #b3302a;
  }
  * { margin: 0; padding: 0; box-sizing: border-box; }
  html, body { width: 849px; height: 1200px; overflow: hidden; background: var(--paper); }
  .flyer {
    position: relative;
    width: 849px;
    height: 1200px;
    background: var(--paper);
    color: var(--ink);
    font-family: "Open Sans", Arial, sans-serif;
    text-align: center;
    overflow: hidden;
  }
  .hero-photo {
    position: absolute;
    left: 0; top: 720px;
    width: 849px; height: 480px;
    background:
      radial-gradient(ellipse 46% 30% at 48% 58%, var(--car) 0%, rgba(179,48,42,0.85) 45%, rgba(179,48,42,0) 100%),
      linear-gradient(to bottom, var(--paper) 0%, #e6e4e2 22%, #c4c1be 50%, var(--track) 78%, #d9d7d5 100%);
  }
  .brand {
    position: absolute;
    top: 70px; left: 0; width: 100%;
    font-family: "Montserrat", Arial, sans-serif;
    font-weight: 700;
    color: var(--brand);
    letter-spacing: 4px;
  }
  .brand-name { font-size: 52px; line-height: 1.1; }
  .brand-sub { font-size: 28px; letter-spacing: 8px; margin-top: 6px; }
  .content { position: absolute; top: 268px; left: 0; width: 100%; padding: 0 70px; }
  .presents {
    font-family: "Montserrat", Arial, sans-serif;
    font-weight: 600;
    font-size: 19px;
    letter-spacing: 1.5px;
    color: var(--accent);
    text-transform: uppercase;
  }
  .title {
    font-family: "Montserrat", Arial, sans-serif;
    font-weight: 600;
    font-size: 44px;
    line-height: 1.1;
    margin-top: 22px;
    white-space: nowrap;
  }
  .subtitle {
    font-family: "Montserrat", Arial, sans-serif;
    font-weight: 500;
    font-size: 34px;
    margin-top: 6px;
  }
  .host { font-size: 22px; font-weight: 600; margin-top: 20px; }
  .details { font-size: 20px; line-height: 1.45; margin: 22px auto 0; max-width: 690px; }
  .date {
    font-family: "Montserrat", Arial, sans-serif;
    font-weight: 600;
    font-size: 31px;
    color: var(--accent);
    margin-top: 38px;
  }
  .gratis { font-size: 21px; margin-top: 22px; }
  .rsvp { font-size: 19px; margin-top: 24px; }
  .partners {
    position: absolute;
    bottom: 22px; left: 0; width: 100%;
    display: flex; justify-content: center; gap: 60px;
    font-family: "Montserrat", Arial, sans-serif;
    font-weight: 700;
    font-size: 17px;
    color: var(--brand);
    letter-spacing: 1px;
    text-transform: uppercase;
  }
</style>
</head>
<body>
  <main class="flyer">
    <div class="hero-photo" role="img" aria-label="Photo of a red Varenne Coupe R7 on a race track, fading into the white page"></div>

    <header class="brand">
      <div class="brand-name">BIRCHWELL</div>
      <div class="brand-sub">MOTOR SOCIETY</div>
    </header>

    <section class="content">
      <p class="presents">Birchwell Motor society presents</p>
      <h1 class="title">Quick Wheels and Rare Vintages</h1>
      <p class="subtitle">(but not while driving)</p>
      <p class="host">Hosted by Halvorn Keep Vault</p>
      <p class="details">Bring your best car(s) and join us to enjoy the party with sommelier selected wines, the best classic and modern cars and hors d'oeuvre catered by Pembry's Shellfish Bar. Live DJ.</p>
      <p class="date">August 26th 3-6 p.m.</p>
      <p class="gratis">This event is gratis.</p>
      <p class="rsvp">RSVP to nora@birchwellmotors.example for address and details</p>
    </section>

    <footer class="partners">
      <span class="partner">Rosalind Market</span>
      <span class="partner">Keep Vault</span>
    </footer>
  </main>
</body>
</html>
```